Design letter head and business card

Hello,

you should design a business card and letter paper for Kranichflug Marketing. In German we write this word with K insteat of C.

Company does not have a logo. But in general, we write Kranichflug Marketing in 2 lines.
First line red: KRANICHFLUG
Second line gray: MARKETING

Red (or wine red) and Gray / Black are our favorite colors.

Company slogan: "Fresh Ground Online Marketing".

Company offers SEO, SEM, SEA, AdWords, Conversion Optimization, Online Markting Consulting ...

The website is old, please do not use this as base for your task.

German letter paper sizes:
Viawable Dimensions : 210 x 297 mm
Needed file dimensions: 212 x 299 mm

Informations to include:

Address:
Kranichflug Marketing GmbH
Lindenweg 23
71592 Weinstadt
Germany

Geschäftsführer | CEO: Bernhard Olzner

Phone: +49 (0) 7151 846 27 05

Fax: +49 (0) 7151 846 27 88

Mail: info@kranichflug-beispiel.de

Web: www.kranichflug-beispiel.de

Amtsgericht Suttgart, HRB 537264

Bank: Rosenauer Bank
IBAN: DE827315480900XXXXXXXX
BIC: GENODES1RSQ

Thanks

Bernhard

Target Market(s)

People who likes to win the online marketing game.

Industry/Entity Type

Business

Contact Information for Business Card

Here is the personal text on the card:

Name:
Bernhard Olzner

Title:
Geschäftsführer | CEO

Address:
Kranichflug Marketing GmbH
Lindenweg 23
71592 Weinstadt
Germany

Phone:
+49 (0) 7151 846 27 05

Fax:
+49 (0) 7151 846 27 88

Mail:
olzner@kranichflug-beispiel.de

Web:
www.kranichflug-beispiel.de

Business Card:
Viewable Dimensions: 85 x 55 mm
Needed file dimensions: 87 x 57mm

Font styles to use
Sans Serif

Requirements
Nice to have
• It would be great to see the dynamics of a helicopter.

```html
<!DOCTYPE html>
<html lang="de">
<head>
<meta charset="utf-8">
<title>Kranichflug Marketing – Visitenkarte</title>
<link rel="stylesheet" href="https://fonts.googleapis.com/css2?family=Saira+Condensed:wght@400;700&display=swap">
<style>
  :root {
    --card-grey: #d1d2d4;
    --mark-grey-light: #c4c5c7;
    --mark-grey-dark: #a9aaac;
    --wine-red: #8b1f24;
    --ink: #2a2a2b;
  }
  html, body {
    margin: 0;
    padding: 0;
    overflow: hidden;
    background: var(--card-grey);
  }
  .card {
    position: relative;
    width: 1200px;
    height: 667px;
    background: var(--card-grey);
    overflow: hidden;
    font-family: "Saira Condensed", "Arial Narrow", sans-serif;
  }
  .edge-band {
    position: absolute;
    top: 148px;
    width: 64px;
    height: 370px;
    background: var(--wine-red);
  }
  .edge-band--left { left: 0; }
  .edge-band--right { right: 0; }

  .brand-mark {
    position: absolute;
    left: 460px;
    top: 62px;
    width: 280px;
    height: 244px;
    border-radius: 12px;
    background: linear-gradient(160deg, var(--mark-grey-light), var(--mark-grey-dark));
  }

  .brand-name {
    position: absolute;
    left: 0;
    right: 0;
    top: 334px;
    margin: 0;
    text-align: center;
    font-weight: 700;
    font-size: 76px;
    line-height: 63px;
    letter-spacing: 2px;
    text-transform: uppercase;
  }
  .brand-name span { display: block; }
  .brand-name__first { color: var(--ink); }
  .brand-name__second { color: var(--wine-red); }

  .slogan {
    position: absolute;
    left: 0;
    right: 0;
    top: 468px;
    margin: 0;
    text-align: center;
    font-weight: 400;
    font-size: 37px;
    color: var(--ink);
  }
  .website {
    position: absolute;
    left: 0;
    right: 0;
    top: 558px;
    margin: 0;
    text-align: center;
    font-weight: 400;
    font-size: 34px;
    color: var(--wine-red);
  }
</style>
</head>
<body>
  <main class="card">
    <div class="edge-band edge-band--left"></div>
    <div class="edge-band edge-band--right"></div>

    <div class="brand-mark" role="img" aria-label="Platz für die Bildmarke von Kranichflug Marketing"></div>

    <h1 class="brand-name">
      <span class="brand-name__first">Kranichflug</span>
      <span class="brand-name__second">Marketing</span>
    </h1>
    <p class="slogan">Fresh Ground Online Marketing</p>
    <p class="website">www.kranichflug-beispiel.de</p>
  </main>
</body>
</html>
```